Business Card Design

Company is a Commercial Building Company specialising in New Construction and existing refurbishments

Industry/Entity Type

Business

Contact Information for Business Card

Liam Porter
Construction Manager
E Liam@marshbuilding.com.au
M 0400 213 594
Mail 14 Tarrant Rise Seabrook Vale WA 6299

```html
<!DOCTYPE html>
<html lang="en">
<head>
<meta charset="utf-8">
<title>Marsh Building &amp; Construction – Business Card</title>
<link href="https://fonts.googleapis.com/css2?family=Saira:wght@400;500&display=swap" rel="stylesheet">
<style>
  :root {
    --orange: #f28c1f;
    --cyan: #08b5d6;
    --ink: #2c3345;
    --paper: #ffffff;
    --backdrop: #e4e1de;
  }
  * { box-sizing: border-box; margin: 0; padding: 0; }
  html, body {
    width: 1200px; height: 997px; overflow: hidden;
    background: var(--backdrop);
    font-family: "Saira", Arial, sans-serif;
    color: var(--ink);
  }
  .card {
    position: absolute;
    width: 640px; height: 366px;
    background: var(--paper);
    box-shadow: 0 6px 18px rgba(0,0,0,0.12);
    overflow: hidden;
  }
  /* Back of card */
  .card-back { left: 280px; top: 90px; }
  .band { position: absolute; left: 0; right: 0; height: 22px; display: flex; }
  .band-top { top: 0; }
  .band-bottom { bottom: 0; }
  .band span { display: block; height: 100%; }
  .band-top .seg-orange { width: 22%; background: var(--orange); }
  .band-top .seg-cyan { flex: 1; background: var(--cyan); }
  .band-bottom .seg-orange { width: 76%; background: var(--orange); }
  .band-bottom .seg-cyan { flex: 1; background: var(--cyan); }
  .brand-centre {
    position: absolute; left: 0; right: 0; top: 0; bottom: 0;
    display: flex; align-items: center; justify-content: center; gap: 14px;
  }
  .brand-mark { width: 22px; height: 22px; background: var(--cyan); }
  .brand-centre .brand-name {
    font-size: 34px; font-weight: 500; letter-spacing: 1px; color: var(--cyan);
  }

  /* Front of card */
  .card-front { left: 280px; top: 540px; }
  .side-band { position: absolute; left: 0; top: 0; bottom: 0; width: 24px; display: flex; flex-direction: column; }
  .side-band .seg-orange { height: 66%; background: var(--orange); }
  .side-band .seg-cyan { flex: 1; background: var(--cyan); }
  .brand-corner {
    position: absolute; right: 34px; top: 48px; text-align: right;
    font-size: 20px; font-weight: 500; line-height: 1.15; letter-spacing: 0.5px; color: var(--ink);
  }
  .person { position: absolute; left: 70px; top: 124px; }
  .person-name { font-size: 27px; font-weight: 500; letter-spacing: 1px; text-transform: uppercase; }
  .person-role { font-size: 15px; font-weight: 400; margin-top: -2px; padding-left: 14px; }
  .contact { position: absolute; left: 70px; bottom: 44px; list-style: none; font-size: 15px; line-height: 1.35; }
  .contact li { display: flex; align-items: center; gap: 8px; }
  .contact svg { width: 13px; height: 13px; flex: none; }
  .contact .no-icon { padding-left: 21px; }
</style>
</head>
<body>
  <section class="card card-back" aria-label="Card back">
    <div class="band band-top"><span class="seg-orange"></span><span class="seg-cyan"></span></div>
    <div class="brand-centre">
      <span class="brand-mark"></span>
      <span class="brand-name">MARSH BUILDING</span>
    </div>
    <div class="band band-bottom"><span class="seg-orange"></span><span class="seg-cyan"></span></div>
  </section>

  <section class="card card-front" aria-label="Card front">
    <div class="side-band"><span class="seg-orange"></span><span class="seg-cyan"></span></div>
    <div class="brand-corner">MARSH BUILDING<br>&amp; CONSTRUCTION</div>
    <div class="person">
      <h1 class="person-name">Liam Porter</h1>
      <p class="person-role">Construction Manager</p>
    </div>
    <ul class="contact">
      <li>
        <svg viewBox="0 0 13 13" aria-hidden="true"><rect x="3" y="0.8" width="7" height="11.4" rx="1.4" fill="none" stroke="currentColor" stroke-width="1.3"/></svg>
        0400 213 594
      </li>
      <li>
        <svg viewBox="0 0 13 13" aria-hidden="true"><rect x="0.7" y="2.5" width="11.6" height="8" fill="none" stroke="currentColor" stroke-width="1.3"/><path d="M0.7 2.5 L6.5 7 L12.3 2.5 M0.7 10.5 L5 6 M12.3 10.5 L8 6" fill="none" stroke="currentColor" stroke-width="1.2"/></svg>
        Liam@marshbuilding.com.au
      </li>
      <li class="no-icon">14 Tarrant Rise Seabrook Vale WA 6299</li>
    </ul>
  </section>
</body>
</html>
```